Verdanith Website Concept

We would like a one page website. Please refer to the attached files for more information.

Please reference file attachment version 1.1.

```html
<!DOCTYPE html>
<html lang="en">
<head>
<meta charset="utf-8">
<title>Verdanith — Financial Security</title>
<link href="https://fonts.googleapis.com/css2?family=Nunito+Sans:wght@300;400;600&family=Source+Sans+3:wght@400;600&display=swap" rel="stylesheet">
<style>
:root{
  --navy:#2c3574;
  --nav:#3b4a8c;
  --nav-dark:#2f3c78;
  --blue:#1aa3dc;
  --phone:#1a8fd0;
  --text:#555;
  --title:#333;
  --line:#e2e2e2;
  --panel:#f2f2f2;
  --card:#f5f5f5;
  --footer:#3a3a3a;
  --white:#fff;
}
*{margin:0;padding:0;box-sizing:border-box}
html,body{width:673px;height:1200px;overflow:hidden;background:var(--white)}
body{position:relative;font-family:"Source Sans 3",Arial,sans-serif;color:var(--text)}
.abs{position:absolute}
.brand{left:74px;top:12px;display:flex;align-items:center;gap:7px}
.brand-mark{width:24px;height:24px;border-radius:50%;background:var(--navy)}
.brand-name{font-family:"Nunito Sans",sans-serif;font-size:17px;color:var(--navy);letter-spacing:.5px}
.hotline{left:472px;top:13px;display:flex;gap:8px;align-items:center}
.hotline-label{font-size:8.5px;color:#444}
.hotline-number{font-size:11.5px;color:var(--phone)}
.nav{left:0;top:51px;width:673px;height:27px;background:linear-gradient(var(--nav),var(--nav-dark))}
.nav ul{list-style:none;position:absolute;left:68px;top:0;display:flex;height:27px}
.nav li{color:var(--white);font-size:7.5px;font-weight:600;padding:0 11px;line-height:27px;border-right:1px solid rgba(255,255,255,.25)}
.nav li:last-child{border-right:none}
.hero{left:73px;top:94px;width:527px;height:248px;background:linear-gradient(110deg,#8f9c7a 0%,#b6b8a6 35%,#c9cbc2 60%,#a7a593 100%)}
.hero-title{right:62px;top:42px;text-align:right;font-family:"Nunito Sans",sans-serif;font-size:21px;line-height:28px;color:var(--navy)}
.hero-copy{right:65px;top:138px;text-align:right;font-size:7.5px;line-height:13px;color:#333;width:190px}
.btn{background:var(--blue);color:var(--white);font-size:7.5px;display:flex;align-items:center;justify-content:center;border-radius:1px}
.hero .btn{left:385px;top:177px;width:75px;height:20px}
.arrow{top:124px;width:10px;height:12px}
.section-title{left:0;width:673px;text-align:center;font-family:"Nunito Sans",sans-serif;font-size:14px;color:var(--title)}
.rule{height:1px;background:var(--line)}
.para{font-size:7.3px;line-height:15.2px}
.card{top:580px;width:124px;height:174px;background:var(--card);border:1px solid #eee}
.card-photo{position:absolute;left:6px;top:8px;width:110px;height:70px}
.card-title{position:absolute;left:4px;right:4px;top:90px;text-align:center;font-family:"Nunito Sans",sans-serif;font-size:9.5px;line-height:13px;color:var(--title)}
.card-copy{position:absolute;left:8px;right:8px;text-align:center;font-size:7px;line-height:12.3px}
.form{left:73px;top:974px;width:527px;height:143px;background:var(--panel)}
.field{background:var(--white);border:1px solid #ddd;font-size:6.8px;color:#999;padding-left:9px;display:flex;align-items:center}
.field.select{font-style:italic;justify-content:space-between;padding-right:9px}
.footer{left:0;top:1147px;width:673px;height:53px;background:var(--footer)}
.footer-copy{left:94px;top:20px;font-size:7.3px;color:#ddd}
.social{top:11px;width:22px;height:22px;border-radius:50%;border:1.5px solid #ccc;background:#555}
</style>
</head>
<body>
<header>
  <div class="abs brand"><span class="brand-mark"></span><span class="brand-name">Verdanith</span></div>
  <div class="abs hotline">
    <svg width="26" height="26" viewBox="0 0 26 26"><circle cx="13" cy="13" r="12" fill="none" stroke="#ddd"/><rect x="9" y="10" width="8" height="6" rx="1" fill="#ccc"/></svg>
    <div><div class="hotline-label">24 Hour Customer Service</div><div class="hotline-number">1800-302-915</div></div>
  </div>
  <nav class="abs nav"><ul><li>HOME</li><li>ABOUT US</li><li>SERVICES</li><li>TRAINING</li><li>MEDIA &amp; EVENTS</li><li>CAREERS</li><li>CONTACT US</li></ul></nav>
</header>

<section class="abs hero" role="img" aria-label="Young plant sprouting among a pile of coins">
  <svg class="abs arrow" style="left:14px" viewBox="0 0 10 12"><path d="M8 1 3 6l5 5" fill="none" stroke="#444" stroke-width="2"/></svg>
  <svg class="abs arrow" style="left:504px" viewBox="0 0 10 12"><path d="M2 1l5 5-5 5" fill="none" stroke="#fff" stroke-width="2"/></svg>
  <h1 class="abs hero-title" style="font-weight:400">We are a<br>financial security<br>company</h1>
  <p class="abs hero-copy">Our firm was created as the result of a specific threat to two of our founders resulting from a private equity</p>
  <div class="abs btn">Learn More</div>
</section>

<h2 class="abs section-title" style="top:381px;font-weight:400">Company Description</h2>
<div class="abs rule" style="left:242px;top:402px;width:190px"></div>
<p class="abs para" style="left:78px;top:413px;width:517px;text-align:center">Verdanith is a United States-based tier one security firm specializing in the protection of financial services professionals, executives and their families. We manage engagements resulting from general and specific threats throughout the United States and abroad on behalf of our domestic clients. We deliver our services exclusively through associates and contractors with United States special operations, secret service.</p>
<div class="abs btn" style="left:305px;top:470px;width:62px;height:20px">Learn More</div>
<div class="abs rule" style="left:73px;top:512px;width:527px"></div>

<h2 class="abs section-title" style="top:537px;font-weight:400">Service Offerings</h2>
<div class="abs rule" style="left:253px;top:558px;width:168px"></div>

<article class="abs card" style="left:73px">
  <div class="card-photo" role="img" aria-label="Hand marking a chart on paper" style="background:linear-gradient(135deg,#5a5048,#d8dde4 55%,#9fb6cf)"></div>
  <h3 class="card-title" style="font-weight:400">Threat Assessment</h3>
  <p class="card-copy" style="top:111px">If you have a general or specific threat you would like to have assessed, it will be our privilege to evaluate</p>
</article>
<article class="abs card" style="left:207px">
  <div class="card-photo" role="img" aria-label="Torn paper revealing a risk word on denim blue" style="background:linear-gradient(90deg,#2e4560,#cfd3d6 40%,#e8e8e4 80%,#3a5270)"></div>
  <h3 class="card-title" style="font-weight:400">Threat Avoidance Plan &amp;<br>Dossier Creation</h3>
  <p class="card-copy" style="top:124px">If you have a general or specific threat you would like to have assessed to evaluate</p>
</article>
<article class="abs card" style="left:342px">
  <div class="card-photo" role="img" aria-label="Security agent in a dark suit beside a car" style="background:linear-gradient(90deg,#8a9096,#2a2c30 40%,#2a2c30 60%,#9aa0a6)"></div>
  <h3 class="card-title" style="font-weight:400">Elite Executive Protection</h3>
  <p class="card-copy" style="top:111px">If you have a general or specific threat you would like to have assessed, it will be our privilege to evaluate</p>
</article>
<article class="abs card" style="left:476px">
  <div class="card-photo" role="img" aria-label="Worker in blue overalls holding a clipboard" style="background:linear-gradient(180deg,#f2f2f2,#8a8f99 55%,#2d5bb0)"></div>
  <h3 class="card-title" style="font-weight:400">Threat Avoidance Plan &amp;<br>Dossier Maintenance</h3>
  <p class="card-copy" style="top:124px">If you have a general or specific threat you would like to have assessed to evaluate</p>
</article>

<div class="abs rule" style="left:73px;top:778px;width:527px"></div>

<h2 class="abs" style="left:74px;top:794px;font-family:'Nunito Sans',sans-serif;font-size:14px;font-weight:400;color:var(--title)">How to Contact Verdanith</h2>
<p class="abs para" style="left:74px;top:819px;width:388px">If you have a general or specific threat you would like to have assessed, it will be our privilege to evaluate your circumstances and provide you with an opinion of how to best address your security needs. Not all security circumstances require tier one professionals. It will be our pleasure to direct you to other firms in your market.</p>
<div class="abs btn" style="left:74px;top:874px;width:63px;height:20px">Learn More</div>
<div class="abs" role="img" aria-label="Group of business people holding question mark signs" style="left:477px;top:802px;width:123px;height:82px;background:linear-gradient(180deg,#e4e4e4,#bfbcb8 55%,#4a4a52)"></div>

<div class="abs rule" style="left:73px;top:916px;width:527px"></div>

<h2 class="abs section-title" style="top:945px;font-weight:400">Request for Consultation</h2>
<form class="abs form">
  <div class="abs field" style="left:15px;top:20px;width:141px;height:20px">Enter your Full Name</div>
  <div class="abs field" style="left:173px;top:20px;width:140px;height:20px">Enter your Email</div>
  <div class="abs field" style="left:330px;top:20px;width:141px;height:20px">Enter your Contact No.</div>
  <div class="abs field" style="left:15px;top:52px;width:141px;height:20px">Enter your Address</div>
  <div class="abs field select" style="left:173px;top:52px;width:140px;height:20px">---Select Your State ----<svg width="7" height="5" viewBox="0 0 7 5"><path d="M1 1l2.5 2.5L6 1" fill="none" stroke="#555"/></svg></div>
  <div class="abs field select" style="left:330px;top:52px;width:141px;height:20px">----Select Your City ----<svg width="7" height="5" viewBox="0 0 7 5"><path d="M1 1l2.5 2.5L6 1" fill="none" stroke="#555"/></svg></div>
  <div class="abs field" style="left:15px;top:83px;width:124px;height:20px">Enter ZipCode</div>
  <div class="abs field" style="left:151px;top:84px;width:264px;height:40px;align-items:flex-start;padding-top:7px">Leave Message</div>
  <div class="abs btn" style="left:426px;top:104px;width:51px;height:20px;font-weight:600">SUBMIT</div>
</form>

<footer class="abs footer">
  <p class="abs footer-copy">Copyright ©2014 Yoursite All Rights Reserved.</p>
  <span class="abs social" style="left:523px"></span>
  <span class="abs social" style="left:550px"></span>
  <span class="abs social" style="left:577px"></span>
</footer>
</body>
</html>
```